Patent Law

Need to develop a home page for a patent lawyer.

Colors should go with logo, blues...

Company Name- Velun Tresk, PLLC

Company Overview-

I am an Intellectual Property Lawyer and focus on patents, copyrights, trademarks, & trade secrets. I work with small businesses and start ups in the chemical and biotech industries.

Why Us-

I am small firm that can provide large-firm service at a reasonable price. I also can charge flat-fees for entreprenuers in certain practice areas.

Services-
Intellectual Property
Patents
Copyrights
Trademarks
Trade secrets
Healthcare Compliance
Elder law
Wills
Trusts

Website we like-
http://www.quorvantlegal.example/ - within industry!!
http://www.daltrowemiko.example/
http://ulbrixtane.example/
http://thegravelcounsel.example/

Target Market(s)

My customers will be small business, specifically small start-up companies in the chemical and biotech arena.

Industry/Entity Type

Trade

Requirements
Must have
• Colors should go with logo, blues...

```html
<!DOCTYPE html>
<html lang="en">
<head>
<meta charset="utf-8">
<title>Velun Tresk, PLLC</title>
<link href="https://fonts.googleapis.com/css2?family=Open+Sans:wght@300;400;600;700&display=swap" rel="stylesheet">
<style>
:root{
  --blue:#1e5aa8;
  --blue-dark:#1b4d98;
  --blue-light:#3a8fd0;
  --heading:#234f9a;
  --link:#1a6fb8;
  --text:#333;
  --muted:#7a7a7a;
  --panel:#f3f3f3;
  --rule:#d6d6d6;
  --footer-top:#3d3d3d;
  --footer-bottom:#242424;
  --tick:#3a8fd0;
}
*{box-sizing:border-box;margin:0;padding:0}
html,body{width:1200px;height:1162px;overflow:hidden;background:#fff}
body{position:relative;font-family:"Open Sans",Arial,sans-serif;color:var(--text)}
.abs{position:absolute}

/* header */
.brand{left:100px;top:100px;display:flex;align-items:center;gap:10px}
.brand-dot{width:22px;height:22px;border-radius:50%;background:var(--blue)}
.brand-name{font-size:21px;font-weight:600;color:#555;letter-spacing:.5px}
.call{right:427px;top:31px;text-align:right}
.call-label{font-size:14px;color:#555}
.call-number{font-size:20px;font-weight:600;color:var(--blue);line-height:1.2}
.phone-icon{left:782px;top:40px}
.divider{left:850px;top:29px;width:1px;height:49px;background:#ddd}
.addr{right:147px;top:32px;text-align:right;font-size:13px;color:#555;line-height:21px}
.pin-icon{left:1064px;top:38px}
.nav{left:644px;top:126px;display:flex;align-items:center;font-size:14.5px;color:#333}
.nav a{color:inherit;text-decoration:none;margin-right:30px}
.nav a.active{background:linear-gradient(#2f86d2,#1c5fae);color:#fff;padding:4px 11px;border-radius:3px;margin-right:21px}

/* hero */
.hero{left:0;top:188px;width:1200px;height:427px;overflow:hidden;
  background:linear-gradient(180deg,var(--blue-light) 0%,#2a6fb8 55%,var(--blue-dark) 100%)}
.hero-sheen{position:absolute;inset:0;background:linear-gradient(120deg,transparent 55%,rgba(255,255,255,.08) 55%,rgba(255,255,255,.08) 80%,transparent 80%)}
.hero-photo{position:absolute;left:678px;top:21px;width:396px;height:406px;border-radius:180px 180px 0 0;
  background:linear-gradient(180deg,#c9cdd4 0%,#8f96a1 60%,#6f7682 100%)}
.hero-copy{position:absolute;left:181px;top:92px;color:#fff;width:420px}
.hero-kicker{font-size:38px;font-weight:700;line-height:1.2}
.hero-title{font-size:38px;font-weight:300;line-height:1.3}
.hero-text{margin-top:12px;font-size:14.5px;line-height:25px}
.btn-light{display:inline-block;margin-top:14px;background:#f1f1f1;color:#444;font-size:15px;font-weight:600;padding:7px 14px;border-radius:3px}
.slider-arrows{position:absolute;left:573px;top:384px;display:flex;gap:3px}
.slider-arrows span{width:25px;height:25px;border-radius:50%;background:#c9ccd2;display:flex;align-items:center;justify-content:center}

/* columns */
.col{top:648px;width:313px}
.col h2{font-size:31px;font-weight:300;color:var(--heading);height:51px}
.why-photo{width:313px;height:155px;background:linear-gradient(135deg,#5b6a80,#c7cdd6 60%,#eef0f3)}
.why-text{margin-top:25px;font-size:13.5px;line-height:23px;color:#333}
.btn-grey{position:absolute;display:inline-block;background:linear-gradient(#9a9a9a,#6e6e6e);color:#fff;font-size:13.5px;font-weight:600;padding:6px 11px;border-radius:3px}
.panel{background:var(--panel);border-top:1px solid var(--rule);border-bottom:1px solid var(--rule);height:263px}
.services{list-style:none;padding:13px 0 0 26px}
.services li{display:flex;align-items:center;gap:9px;height:27.1px;font-size:14px;font-weight:600;color:var(--link);text-transform:uppercase}
.contacts{padding:20px 0 0 24px;font-size:14px;color:var(--muted)}
.contact-row{display:flex;align-items:flex-start;gap:22px;line-height:23px}
.contact-row svg{flex:none;margin-top:2px}

/* footer */
.footer{left:0;top:1056px;width:1200px;height:106px;background:linear-gradient(var(--footer-top),var(--footer-bottom));color:#ddd;font-size:13.5px}
.footer-links{position:absolute;left:101px;top:24px}
.footer-links a{color:#ddd;text-decoration:none}
.footer-links .sep{margin:0 12px}
.copyright{position:absolute;left:101px;top:58px}
.social{position:absolute;left:1045px;top:41px;display:flex;gap:6px}
.social span{width:24px;height:24px;border-radius:3px;background:#3b6fb6}
.social span+span{background:#3fb2e5}
</style>
</head>
<body>

<header>
  <div class="abs brand"><span class="brand-dot"></span><span class="brand-name">VELUN TRESK, PLLC</span></div>
  <div class="abs call"><div class="call-label">Call us Today</div><div class="call-number">555 204 7731</div></div>
  <svg class="abs phone-icon" width="30" height="30" viewBox="0 0 30 30"><path d="M4 5c3-3 6-2 7 1l1 3-3 3c2 4 5 7 9 9l3-3 3 1c3 1 4 4 1 7-3 3-10 1-16-5S1 8 4 5z" fill="#777"/></svg>
  <div class="abs divider"></div>
  <div class="abs addr">18, Harwell Court,<br>Linden Row, Marrow - 40217</div>
  <svg class="abs pin-icon" width="20" height="30" viewBox="0 0 20 30"><path d="M10 1a9 9 0 0 0-9 9c0 7 9 19 9 19s9-12 9-19a9 9 0 0 0-9-9z" fill="#777"/><circle cx="10" cy="10" r="3.5" fill="#fff"/></svg>
  <nav class="abs nav">
    <a class="active" href="#">HOME</a><a href="#">ABOUT US</a><a href="#">SERVICES</a><a href="#">NEWS</a><a href="#">CONTACT US</a>
  </nav>
</header>

<section class="abs hero">
  <div class="hero-sheen"></div>
  <div class="hero-photo" role="img" aria-label="Portrait photo of a smiling senior attorney in a grey suit"></div>
  <div class="hero-copy">
    <div class="hero-kicker">WELCOME TO</div>
    <div class="hero-title">VELUN TRESK, PLLC</div>
    <p class="hero-text">Curabitur ut eros pharetra, congue nibh sed, pulvinar enim. Vivamus eleifend erat sit amet tortor aliquet, vel cursus orci lobortis. Aliquam erat volutpat. In sapien orci.</p>
    <span class="btn-light">Know more</span>
  </div>
  <div class="slider-arrows">
    <span><svg width="10" height="12" viewBox="0 0 10 12"><path d="M7 1 2 6l5 5" stroke="#555" stroke-width="2.5" fill="none"/></svg></span>
    <span><svg width="10" height="12" viewBox="0 0 10 12"><path d="M3 1l5 5-5 5" stroke="#555" stroke-width="2.5" fill="none"/></svg></span>
  </div>
</section>

<section class="abs col" style="left:100px">
  <h2>WHY US</h2>
  <div class="why-photo" role="img" aria-label="Photo of a business team with a smiling woman in front"></div>
  <p class="why-text">Curabitur ut eros pharetra, congue nibh sed, pulvinar enim. Vivamus eleifend erat sit amet tortor aliquet, vel cursus orci lobortis. Aliquam erat volutpat. In sapien orci.</p>
  <span class="btn-grey" style="left:1px;top:332px">Read more</span>
</section>

<section class="abs col" style="left:444px">
  <h2>WHAT WE DO</h2>
  <div class="panel">
    <ul class="services">
      <li><svg width="12" height="10" viewBox="0 0 12 10"><path d="M1 5l3.5 3.5L11 1.5" stroke="var(--tick)" stroke-width="2" fill="none"/></svg>Intellectual Property</li>
      <li><svg width="12" height="10" viewBox="0 0 12 10"><path d="M1 5l3.5 3.5L11 1.5" stroke="var(--tick)" stroke-width="2" fill="none"/></svg>Patents</li>
      <li><svg width="12" height="10" viewBox="0 0 12 10"><path d="M1 5l3.5 3.5L11 1.5" stroke="var(--tick)" stroke-width="2" fill="none"/></svg>Copyrights</li>
      <li><svg width="12" height="10" viewBox="0 0 12 10"><path d="M1 5l3.5 3.5L11 1.5" stroke="var(--tick)" stroke-width="2" fill="none"/></svg>Trademarks</li>
      <li><svg width="12" height="10" viewBox="0 0 12 10"><path d="M1 5l3.5 3.5L11 1.5" stroke="var(--tick)" stroke-width="2" fill="none"/></svg>Trade Secrets</li>
      <li><svg width="12" height="10" viewBox="0 0 12 10"><path d="M1 5l3.5 3.5L11 1.5" stroke="var(--tick)" stroke-width="2" fill="none"/></svg>Healthcare Compliance</li>
      <li><svg width="12" height="10" viewBox="0 0 12 10"><path d="M1 5l3.5 3.5L11 1.5" stroke="var(--tick)" stroke-width="2" fill="none"/></svg>Elder Law</li>
      <li><svg width="12" height="10" viewBox="0 0 12 10"><path d="M1 5l3.5 3.5L11 1.5" stroke="var(--tick)" stroke-width="2" fill="none"/></svg>Wills</li>
      <li><svg width="12" height="10" viewBox="0 0 12 10"><path d="M1 5l3.5 3.5L11 1.5" stroke="var(--tick)" stroke-width="2" fill="none"/></svg>Trusts</li>
    </ul>
  </div>
  <span class="btn-grey" style="left:0;top:332px">Contact us</span>
</section>

<section class="abs col" style="left:788px">
  <h2>COTNACT INFO</h2>
  <div class="panel contacts">
    <div class="contact-row" style="height:66px">
      <svg width="20" height="22" viewBox="0 0 20 22"><rect x="1" y="2" width="18" height="19" fill="#8a8a8a"/><rect x="5" y="5" width="3" height="12" fill="#f3f3f3"/><rect x="12" y="5" width="3" height="12" fill="#f3f3f3"/></svg>
      <div>18, Harwell Court, Linden Row<br>Marrow - 40217</div>
    </div>
    <div class="contact-row" style="height:52px">
      <svg width="22" height="22" viewBox="0 0 30 30"><path d="M4 5c3-3 6-2 7 1l1 3-3 3c2 4 5 7 9 9l3-3 3 1c3 1 4 4 1 7-3 3-10 1-16-5S1 8 4 5z" fill="#8a8a8a"/></svg>
      <div>Phone: 555 204 7731</div>
    </div>
    <div class="contact-row" style="height:57px">
      <svg width="22" height="22" viewBox="0 0 22 22"><rect x="1" y="6" width="20" height="15" rx="1" fill="#8a8a8a"/><rect x="5" y="1" width="12" height="7" fill="#aaa"/><rect x="11" y="10" width="8" height="2" fill="#f3f3f3"/><rect x="11" y="14" width="8" height="2" fill="#f3f3f3"/></svg>
      <div>Fax : 555 204 7790</div>
    </div>
    <div class="contact-row">
      <svg width="22" height="16" viewBox="0 0 22 16"><rect x="0" y="0" width="22" height="16" fill="#8a8a8a"/><path d="M0 0l11 9 11-9" stroke="#f3f3f3" stroke-width="1.5" fill="none"/></svg>
      <div>E-mail : info@veluntreskpllc.example</div>
    </div>
  </div>
</section>

<footer class="abs footer">
  <div class="footer-links"><a href="#">Home</a><span class="sep">|</span><a href="#">About us</a><span class="sep">|</span><a href="#">Services</a><span class="sep">|</span><a href="#">News</a><span class="sep">|</span><a href="#">Contact us</a></div>
  <div class="copyright">Copyright &copy; 2014 &nbsp;Velun Tresk, pllc. &nbsp;All rights reserved.</div>
  <div class="social"><span></span><span></span></div>
</footer>

</body>
</html>
```